Business Card Design

I am an Event and Wedding Planner in need of an eye catching business card featuring my logo (attached), my contact details, and my company tagline (Making every celebration glow with wonder...) I would like the tagline in font similar the logo's font.
Updates
I have just noticed that my logo has a misspelling so for the final design, I will be uploading a corrected logo as soon as I have it.
My apologies.
Reason: Waiting on a corrected logo...Lantern is misspelled and it should say Weddings not Wedding
The logo has been corrected so now Lantern is spelled correctly and it says Weddings instead of Wedding. Please use Edwardian Script ITC as the font for the tagline so it will match the logo. Thank you for your patience.
Target Market(s)
Engaged couples and people hosting milestone celebrations. 25-50 years old, predominately female
Industry/Entity Type
Business
Contact Information for Business Card
Rosalind Merrow, Event Manager / Owner, Mobile: 0491 868 254, Email: rosalind@velvetlanternco.com.au, www.velvetlanternco.com.au, Making every celebration glow with wonder...

```html
<!DOCTYPE html>
<html lang="en">
<head>
<meta charset="utf-8">
<title>Velvet Lantern — Business Card</title>
<link rel="stylesheet" href="https://fonts.googleapis.com/css2?family=Montserrat:wght@400;500&family=Pinyon+Script&display=swap">
<style>
  :root {
    --backdrop: #e6e6e8;
    --card: #ffffff;
    --ink: #1a1a1a;
    --ink-soft: #4a4a4a;
    --rule-grey: #b9b9b9;
    --accent-red: #c8343b;
    --band: #111111;
  }
  * { margin: 0; padding: 0; box-sizing: border-box; }
  html, body { width: 1200px; height: 988px; overflow: hidden; }
  body {
    background: var(--backdrop);
    font-family: "Montserrat", Arial, sans-serif;
    color: var(--ink);
    display: flex;
    flex-direction: column;
    align-items: center;
    justify-content: center;
    gap: 40px;
  }
  .card {
    position: relative;
    width: 760px;
    height: 434px;
    background: var(--card);
    overflow: hidden;
    box-shadow: 0 2px 8px rgba(0,0,0,0.12);
  }
  .card__band {
    position: absolute;
    top: 0; left: 0; right: 0;
    height: 16px;
    background: var(--band);
  }
  .brand {
    position: absolute;
    display: flex;
    align-items: center;
    gap: 14px;
  }
  .brand__name {
    font-weight: 400;
    color: var(--ink);
    letter-spacing: 0.02em;
    white-space: nowrap;
  }
  .brand__dot {
    width: 14px; height: 14px;
    border-radius: 50%;
    background: var(--accent-red);
    flex: none;
  }
  .brand__rule {
    position: absolute;
    height: 1px;
    background: var(--rule-grey);
  }
  .tagline {
    position: absolute;
    font-family: "Pinyon Script", "Great Vibes", cursive;
    color: var(--ink);
    white-space: nowrap;
  }
  /* back */
  .card--back .brand { left: 0; right: 0; top: 170px; justify-content: center; }
  .card--back .brand__name { font-size: 44px; }
  .card--back .brand__rule { left: 230px; right: 230px; top: 240px; }
  .card--back .tagline { left: 0; right: 0; top: 248px; text-align: center; font-size: 30px; }
  /* front */
  .card--front .brand { left: 40px; top: 62px; }
  .card--front .brand__name { font-size: 30px; }
  .card--front .brand__rule { left: 40px; width: 300px; top: 114px; }
  .card--front .tagline { left: 40px; top: 120px; font-size: 23px; }
  .red-rule {
    position: absolute;
    height: 2px;
    background: var(--accent-red);
  }
  .red-rule--upper { left: 360px; right: 0; top: 100px; }
  .red-rule--lower { left: 0; right: 0; top: 372px; }
  .contacts {
    position: absolute;
    left: 400px;
    top: 160px;
    display: flex;
    flex-direction: column;
    gap: 14px;
    font-size: 13px;
    color: var(--ink-soft);
  }
  .contact { display: flex; align-items: center; gap: 10px; white-space: nowrap; }
  .contact svg { width: 17px; height: 17px; flex: none; }
  .person { position: absolute; left: 40px; top: 300px; }
  .person__name {
    font-size: 22px;
    font-weight: 400;
    letter-spacing: 0.08em;
    text-transform: uppercase;
  }
  .person__role {
    margin-top: 4px;
    font-size: 12px;
    letter-spacing: 0.08em;
    text-transform: uppercase;
    color: var(--ink-soft);
  }
</style>
</head>
<body>

  <section class="card card--back">
    <div class="card__band"></div>
    <div class="brand">
      <span class="brand__name">Velvet Lantern</span>
      <span class="brand__dot"></span>
    </div>
    <div class="brand__rule"></div>
    <p class="tagline">Making every celebration glow with wonder...</p>
  </section>

  <section class="card card--front">
    <div class="card__band"></div>
    <div class="brand">
      <span class="brand__name">Velvet Lantern</span>
      <span class="brand__dot"></span>
    </div>
    <div class="brand__rule"></div>
    <p class="tagline">Making every celebration glow with wonder...</p>
    <div class="red-rule red-rule--upper"></div>

    <div class="contacts">
      <div class="contact">
        <svg viewBox="0 0 16 16" aria-hidden="true"><circle cx="8" cy="8" r="8" fill="#1a1a1a"/><path d="M5.5 4.5l1.5 0 .7 2-1 .8a5 5 0 0 0 2 2l.8-1 2 .7v1.5a1 1 0 0 1-1 1A6 6 0 0 1 4.5 5.5a1 1 0 0 1 1-1z" fill="#fff"/></svg>
        <span>0491 868 254</span>
      </div>
      <div class="contact">
        <svg viewBox="0 0 16 16" aria-hidden="true"><circle cx="8" cy="8" r="8" fill="#1a1a1a"/><rect x="4" y="5" width="8" height="6" fill="none" stroke="#fff" stroke-width="1"/><path d="M4 5l4 3.5L12 5" fill="none" stroke="#fff" stroke-width="1"/></svg>
        <span>rosalind@velvetlanternco.com.au</span>
      </div>
      <div class="contact">
        <svg viewBox="0 0 16 16" aria-hidden="true"><circle cx="8" cy="8" r="8" fill="#1a1a1a"/><circle cx="8" cy="8" r="4" fill="none" stroke="#fff" stroke-width="1"/><path d="M4 8h8M8 4c-2 2.5-2 5.5 0 8M8 4c2 2.5 2 5.5 0 8" fill="none" stroke="#fff" stroke-width="0.8"/></svg>
        <span>www.velvetlanternco.com.au</span>
      </div>
      <div class="contact">
        <svg viewBox="0 0 16 16" aria-hidden="true"><circle cx="8" cy="8" r="8" fill="#1a1a1a"/><path d="M8 3.5a3 3 0 0 1 3 3c0 2.2-3 5.5-3 5.5S5 8.7 5 6.5a3 3 0 0 1 3-3z" fill="#fff"/><circle cx="8" cy="6.5" r="1" fill="#1a1a1a"/></svg>
        <span>14 Harbour Lane Fremantle WA</span>
      </div>
    </div>

    <div class="person">
      <h1 class="person__name">Rosalind Merrow</h1>
      <p class="person__role">Event Manager / Owner</p>
    </div>

    <div class="red-rule red-rule--lower"></div>
  </section>

</body>
</html>
```